Business Card Design for Translation Company - Rush

Rush job for a business card designing for a company doing international translations, several Asian and western languages. Already have a logo design (see attached) to use as the basis of the business card design. For the card, we also need the full company name, address, email, and phone number. In addition, my name as I will be the one handing out the cards.

For the logo design, we think the white background would be best. But we will consider using the dark background if you have a great idea for it.

The attached jpeg design has just been approved, but the designer has not yet finalized the file. When we select our final applicant, we will send the finalized file. (Nothing changes except the quality of the data.)

The phone number may change and if so, we will send the new one when we select our applicant.

We must complete the entire process and have a design ready to go to print no later than 01:00 am August 3, New York (East Coast) time.

We look forward to your participation in the project,
Dale

Target Market(s)

Translation clients worldwide.

Industry/Entity Type

Business

Contact Information for Business Card

Company details:

Korvanta Translations International, Ltd.

#207-2836 Wexholm Avenue, Victoria, BC, Canada V9T3K2

jquell@korvantatranslations.example

+1-888-604-7321

Font styles to use
Sans Serif

Requirements
Must have
• Company name, address, email and phone number.
• Also my name:
• Gordon R. Quell
• Director
Nice to have
• Not a demand, but please consider creatively using the horizontal bar.
Should not have
• Cluttered of jumbled appearance.

```html
<!DOCTYPE html>
<html lang="en">
<head>
<meta charset="utf-8">
<title>Korvanta Translations – Business Card</title>
<link rel="stylesheet" href="https://fonts.googleapis.com/css2?family=Montserrat:wght@400;600;700&family=Open+Sans:wght@400;600&display=swap">
<style>
  :root {
    --page-bg: #ecebe8;
    --card-white: #ffffff;
    --brand-orange: #ef7d22;
    --brand-orange-deep: #e4701a;
    --ink-dark: #3b3b3d;
    --ink-soft: #555558;
    --rule-light: #ffffff;
  }
  * { box-sizing: border-box; margin: 0; padding: 0; }
  html, body {
    width: 1200px;
    height: 1024px;
    overflow: hidden;
    background: var(--page-bg);
  }
  .canvas {
    position: relative;
    width: 1200px;
    height: 1024px;
  }
  .card {
    position: absolute;
    width: 720px;
    height: 412px;
    border-radius: 4px;
    box-shadow: 0 6px 18px rgba(0,0,0,0.16);
    overflow: hidden;
  }

  /* Front */
  .card-front {
    left: 90px;
    top: 80px;
    background: var(--card-white);
  }
  .holder {
    position: absolute;
    left: 56px;
    top: 70px;
  }
  .holder-rule {
    width: 150px;
    height: 3px;
    background: var(--brand-orange);
    margin-bottom: 14px;
  }
  .holder-name {
    font-family: "Montserrat", sans-serif;
    font-weight: 700;
    font-size: 19px;
    letter-spacing: 0.5px;
    text-transform: uppercase;
    color: var(--ink-dark);
  }
  .holder-title {
    font-family: "Montserrat", sans-serif;
    font-weight: 400;
    font-size: 16px;
    color: var(--brand-orange);
    margin-top: 3px;
  }
  .brand {
    position: absolute;
    left: 300px;
    top: 58px;
    display: flex;
    align-items: center;
    gap: 14px;
  }
  .brand-dot {
    width: 34px;
    height: 34px;
    border-radius: 50%;
    background: var(--brand-orange);
    flex: none;
  }
  .brand-name {
    font-family: "Montserrat", sans-serif;
    font-weight: 600;
    font-size: 21px;
    letter-spacing: 3px;
    text-transform: uppercase;
    color: var(--ink-dark);
  }
  .brand-rule {
    position: absolute;
    left: 348px;
    top: 104px;
    width: 320px;
    height: 2px;
    background: var(--brand-orange);
  }
  .contact {
    position: absolute;
    left: 348px;
    top: 176px;
    font-family: "Open Sans", sans-serif;
    font-size: 13.5px;
    line-height: 1.55;
    color: var(--ink-soft);
  }
  .contact-label {
    color: var(--brand-orange);
    font-weight: 600;
    margin-right: 4px;
  }
  .contact-company { margin-top: 12px; }
  .stripe-dark {
    position: absolute;
    left: 0;
    right: 0;
    bottom: 34px;
    height: 8px;
    background: var(--ink-dark);
  }
  .stripe-orange {
    position: absolute;
    left: 0;
    right: 0;
    bottom: 0;
    height: 24px;
    background: var(--brand-orange);
  }

  /* Back */
  .card-back {
    left: 390px;
    top: 548px;
    background: linear-gradient(135deg, var(--brand-orange) 0%, var(--brand-orange-deep) 100%);
  }
  .back-field {
    position: absolute;
    inset: 0;
  }
  .back-brand {
    position: absolute;
    left: 0;
    right: 0;
    top: 176px;
    display: flex;
    justify-content: center;
    align-items: center;
    gap: 14px;
  }
  .back-brand .brand-dot {
    background: var(--card-white);
  }
  .back-brand .brand-name {
    color: var(--card-white);
  }
  .back-rule {
    position: absolute;
    left: 230px;
    top: 236px;
    width: 300px;
    height: 2px;
    background: var(--rule-light);
  }
</style>
</head>
<body>
<main class="canvas">

  <section class="card card-front" aria-label="Business card front">
    <div class="holder">
      <div class="holder-rule"></div>
      <p class="holder-name">Gordon R. Quell</p>
      <p class="holder-title">Director</p>
    </div>

    <div class="brand">
      <span class="brand-dot"></span>
      <span class="brand-name">Korvanta Translations</span>
    </div>
    <div class="brand-rule"></div>

    <div class="contact">
      <p><span class="contact-label">P:</span>+1-888-604-7321</p>
      <p><span class="contact-label">E:</span>jquell@korvantatranslations.example</p>
      <p class="contact-company">Korvanta Translations International, Ltd.</p>
      <p>#207-2836 Wexholm Avenue, Victoria, BC,</p>
      <p>Canada V9T3K2</p>
    </div>

    <div class="stripe-dark"></div>
    <div class="stripe-orange"></div>
  </section>

  <section class="card card-back" aria-label="Business card back">
    <div class="back-field" role="img" aria-label="Subtle tone-on-tone orange repeating brand pattern"></div>
    <div class="back-brand">
      <span class="brand-dot"></span>
      <span class="brand-name">Korvanta Translations</span>
    </div>
    <div class="back-rule"></div>
  </section>

</main>
</body>
</html>
```